IT solutions & services company requires stationary makeover

Looking for a consistent modern, professional design across our printed client touch points:
Business Cards
Letterhead
Client proposal
Flyer
Postcard

We provide solutions for SME IT - servers, backups, AV etc, and the ongoing services around them.
we are happy with our logo - please see attached and would like the colour theme to be maintained.

```html
<!DOCTYPE html>
<html lang="en">
<head>
<meta charset="utf-8">
<title>Korvo – Presentation Folder</title>
<link href="https://fonts.googleapis.com/css2?family=Montserrat:wght@300;400;500&display=swap" rel="stylesheet">
<style>
  :root {
    --brand-blue: #17a3dc;
    --brand-blue-deep: #0f86b8;
    --brand-ink: #3b2f2c;
    --paper: #ffffff;
    --paper-shade: #eeeeef;
    --backdrop: #e9e7e4;
    --contact-ink: #2f5f78;
  }
  * { box-sizing: border-box; margin: 0; padding: 0; }
  html, body { width: 1200px; height: 801px; overflow: hidden; }
  body {
    background: var(--backdrop);
    font-family: "Montserrat", sans-serif;
    position: relative;
  }

  /* Outer cover */
  .folder-cover {
    position: absolute;
    left: 40px; top: 23px;
    width: 571px; height: 408px;
    background: linear-gradient(90deg, var(--brand-blue-deep) 0%, var(--brand-blue) 22%, var(--brand-blue) 100%);
    box-shadow: 2px 3px 6px rgba(0,0,0,0.25);
  }
  .cover-brand {
    position: absolute;
    left: 337px; top: 184px;
    display: flex; align-items: center; gap: 12px;
  }
  .brand-dot {
    width: 40px; height: 40px; border-radius: 50%;
    background: var(--brand-ink);
  }
  .cover-brand .brand-name {
    font-weight: 400; font-size: 50px; line-height: 1;
    color: var(--brand-ink); letter-spacing: 1px;
  }
  .cover-contact {
    position: absolute;
    left: 83px; top: 358px; width: 200px;
    text-align: center;
    font-style: italic; font-size: 6.5px; line-height: 10px;
    color: var(--contact-ink);
  }

  /* Inner spread */
  .folder-inside {
    position: absolute;
    left: 581px; top: 365px;
    width: 571px; height: 404px;
    background: var(--paper);
    box-shadow: 3px 4px 8px rgba(0,0,0,0.28);
  }
  .inside-left {
    position: absolute; left: 0; top: 0;
    width: 285px; height: 100%;
    background: linear-gradient(90deg, var(--paper) 0%, var(--paper) 60%, var(--paper-shade) 100%);
  }
  .inside-right {
    position: absolute; left: 285px; top: 0;
    width: 286px; height: 100%;
    background: linear-gradient(90deg, var(--paper-shade) 0%, var(--paper) 12%);
  }
  .pocket { position: absolute; left: 0; bottom: 0; width: 286px; height: 134px; }
  .pocket-brand {
    position: absolute; right: 20px; bottom: 30px;
    display: flex; align-items: center; gap: 5px;
  }
  .pocket-brand .brand-dot { width: 16px; height: 16px; background: var(--paper); }
  .pocket-brand .brand-name {
    font-weight: 400; font-size: 22px; line-height: 1; color: var(--paper);
  }
</style>
</head>
<body>

  <section class="folder-cover" aria-label="Folder outer cover">
    <div class="cover-brand">
      <span class="brand-dot"></span>
      <span class="brand-name">Korvo</span>
    </div>
    <address class="cover-contact">
      03 555 0182<br>
      hello@korvo-it.example<br>
      Level 2, Harbour Lane, Lakeview, NZ<br>
      www.korvo-it.example
    </address>
  </section>

  <section class="folder-inside" aria-label="Folder inner spread">
    <div class="inside-left"></div>
    <div class="inside-right">
      <svg class="pocket" viewBox="0 0 286 134" aria-hidden="true">
        <path d="M0 18 Q150 28 286 0 L286 134 L0 134 Z" fill="var(--brand-blue)"/>
        <path d="M18 38 L120 38 L130 48 L130 84 L122 92 L18 92 Z" fill="var(--paper)"/>
      </svg>
      <div class="pocket-brand">
        <span class="brand-dot"></span>
        <span class="brand-name">Korvo</span>
      </div>
    </div>
  </section>

</body>
</html>
```